Colin Vardek Business card

Hey there, I’m hoping to have a business card designed. I’m in Real estate and just switched to a new Brokerage called: The Harbourline Property Group

The back could just be the company name maybe or whatever looks good!

I’ve attached some logos of our company and some cards my buddy had done up.

On the card:
Colin Vardek
colinvardek@mailora.com
587-412-9065
colinvardek.ca

Target Market(s)

Home buyers and sellers

Industry/Entity Type

Real Estate

Contact Information for Business Card

just looking for a cool and modern design with my picture on it. I like the idea of Black and red being used.

Requirements
Must have
• all the details provided. I'm open to anything. Just want a professional looking card.

```html
<!DOCTYPE html>
<html lang="en">
<head>
<meta charset="UTF-8">
<title>Colin Vardek – Business Card</title>
<link rel="stylesheet" href="https://fonts.googleapis.com/css2?family=Poppins:wght@300;400;700&display=swap">
<style>
  :root {
    --page-bg: #1f1f21;
    --card-bg: #26252b;
    --accent-red: #d3203f;
    --text-white: #ffffff;
    --photo-dark: #1b2230;
    --photo-mid: #3a4150;
    --photo-light: #d9d6d2;
  }
  * { box-sizing: border-box; margin: 0; padding: 0; }
  html, body {
    width: 1200px;
    height: 711px;
    overflow: hidden;
    background: var(--page-bg);
    font-family: "Poppins", sans-serif;
  }
  .canvas {
    position: relative;
    width: 1200px;
    height: 711px;
  }
  .card {
    position: absolute;
    top: 95px;
    width: 300px;
    height: 520px;
    background: var(--card-bg);
    border: 2px solid var(--accent-red);
    overflow: hidden;
  }
  .card--front {
    left: 270px;
    border-radius: 150px 150px 0 0;
  }
  .card--back {
    left: 630px;
    border-radius: 0 0 150px 150px;
  }

  /* Front */
  .agent-photo {
    position: absolute;
    left: 18px;
    top: 70px;
    width: 220px;
    height: 450px;
    border-radius: 110px 110px 0 0;
    background: linear-gradient(180deg, var(--photo-mid) 0%, var(--photo-dark) 45%, var(--photo-dark) 100%);
  }
  .agent-photo::after {
    content: "";
    position: absolute;
    left: 95px;
    top: 150px;
    width: 40px;
    height: 300px;
    background: linear-gradient(180deg, var(--photo-light), rgba(217,214,210,0.6));
    border-radius: 6px;
  }
  .brand-vertical {
    position: absolute;
    right: 16px;
    top: 160px;
    writing-mode: vertical-rl;
    font-weight: 700;
    font-size: 20px;
    line-height: 1;
    letter-spacing: 0.5px;
    color: var(--text-white);
    white-space: nowrap;
  }

  /* Back */
  .brand-mark {
    position: absolute;
    left: 30px;
    top: 44px;
    width: 220px;
    font-weight: 700;
    font-size: 24px;
    line-height: 1.15;
    color: var(--text-white);
  }
  .agent-name {
    position: absolute;
    left: 30px;
    top: 330px;
    font-size: 30px;
    font-weight: 400;
    line-height: 1;
    color: var(--text-white);
    white-space: nowrap;
  }
  .agent-name__first { font-weight: 700; color: var(--accent-red); }
  .agent-name__last { font-weight: 300; }
  .contact-list {
    position: absolute;
    left: 34px;
    top: 380px;
    list-style: none;
  }
  .contact-list__item {
    display: flex;
    align-items: center;
    gap: 9px;
    font-size: 12.5px;
    font-weight: 400;
    color: var(--text-white);
    margin-bottom: 8px;
    white-space: nowrap;
  }
  .contact-list__icon {
    width: 13px;
    height: 13px;
    flex: none;
    fill: var(--accent-red);
  }
</style>
</head>
<body>
<main class="canvas">
  <section class="card card--front">
    <div class="agent-photo" role="img" aria-label="Portrait of Colin Vardek in a dark suit and white shirt"></div>
    <p class="brand-vertical">The Harbourline Property Group</p>
  </section>

  <section class="card card--back">
    <p class="brand-mark">The Harbourline Property Group</p>
    <h1 class="agent-name"><span class="agent-name__first">Colin</span> <span class="agent-name__last">Vardek</span></h1>
    <ul class="contact-list">
      <li class="contact-list__item">
        <svg class="contact-list__icon" viewBox="0 0 24 24" aria-hidden="true"><path d="M6.6 10.8a15.1 15.1 0 0 0 6.6 6.6l2.2-2.2a1 1 0 0 1 1-.25 11.4 11.4 0 0 0 3.6.57 1 1 0 0 1 1 1V20a1 1 0 0 1-1 1A17 17 0 0 1 3 4a1 1 0 0 1 1-1h3.5a1 1 0 0 1 1 1c0 1.250.2 2.460.57 3.6a1 1 0 0 1-.25 1z"/></svg>
        587-412-9065
      </li>
      <li class="contact-list__item">
        <svg class="contact-list__icon" viewBox="0 0 24 24" aria-hidden="true"><path d="M12 2a10 10 0 1 0 0 20 10 10 0 0 0 0-20zm6.9 6h-2.9a15.7 15.7 0 0 0-1.4-3.6A8 8 0 0 1 18.9 8zM12 4a14 14 0 0 1 1.9 4h-3.8A14 14 0 0 1 12 4zM4.3 14a8 8 0 0 1 0-4h3.4a16 16 0 0 0 0 4zm.8 2h2.9a15.7 15.7 0 0 0 1.4 3.6A8 8 0 0 1 5.1 16zM8 8H5.1a8 8 0 0 1 4.3-3.6A15.7 15.7 0 0 0 8 8zm4 12a14 14 0 0 1-1.9-4h3.8A14 14 0 0 1 12 20zm2.3-6H9.7a14.7 14.7 0 0 1 0-4h4.6a14.7 14.7 0 0 1 0 4zm.3 5.6A15.7 15.7 0 0 0 16 16h2.9a8 8 0 0 1-4.3 3.6zm1.7-5.6a16 16 0 0 0 0-4h3.4a8 8 0 0 1 0 4z"/></svg>
        www.colinvardek.ca
      </li>
      <li class="contact-list__item">
        <svg class="contact-list__icon" viewBox="0 0 24 24" aria-hidden="true"><path d="M3 5h18a1 1 0 0 1 1 1v12a1 1 0 0 1-1 1H3a1 1 0 0 1-1-1V6a1 1 0 0 1 1-1zm1 2.3V17h16V7.3l-8 5.2z M5.2 7 12 11.4 18.8 7z"/></svg>
        colinvardek@mailora.com
      </li>
    </ul>
  </section>
</main>
</body>
</html>
```